Business Card Design

New business card design

Target Market(s)

Residential & Commercial Property Managers

Industry/Entity Type

Plumbing Services

Contact Information for Business Card

Name - Rowan Keddle, title - Director, Phone Number - 0431 286 517, email - rowan@tbk-plumbing.com.au, Company ABN - 73 215 904 386,

Font styles to use
Sans Serif

Colors
0054AA
0677BA
7BADD7
CADEEF
E8F1F8

```html
<!DOCTYPE html>
<html lang="en">
<head>
<meta charset="utf-8">
<title>TBK Plumbing Services – Business Card</title>
<link href="https://fonts.googleapis.com/css2?family=Montserrat:wght@400;500;700&display=swap" rel="stylesheet">
<style>
  :root {
    --backdrop: #9a9a9a;
    --card-white: #ffffff;
    --card-navy: #1d222a;
    --ink: #1c2129;
    --accent-blue: #2ca8e0;
  }
  * { margin: 0; padding: 0; box-sizing: border-box; }
  html, body { width: 1093px; height: 1200px; overflow: hidden; }
  body {
    background: var(--backdrop);
    font-family: "Montserrat", sans-serif;
    color: var(--ink);
    position: relative;
  }
  .card {
    position: absolute;
    left: 270px;
    width: 575px;
    height: 358px;
    border-radius: 18px;
    box-shadow: -5px 5px 0 var(--accent-blue);
    overflow: hidden;
  }
  .card--front { top: 225px; background: var(--card-white); }
  .card--back { top: 614px; height: 362px; background: var(--card-navy); }

  .brand-name {
    position: absolute;
    font-weight: 700;
    letter-spacing: 0.3px;
    white-space: nowrap;
  }
  .card--front .brand-name {
    left: 24px; top: 58px;
    width: 300px;
    font-size: 22px;
    line-height: 1;
    color: var(--ink);
  }
  .card--back .brand-name {
    left: 0; right: 0; top: 174px;
    text-align: center;
    font-size: 36px;
    line-height: 1;
    color: var(--card-white);
  }

  .holder {
    position: absolute;
    right: 35px; top: 40px;
    width: 200px;
    text-align: right;
  }
  .holder__name { font-size: 21px; font-weight: 700; line-height: 1.1; }
  .holder__title { font-size: 13px; font-weight: 500; margin-top: 3px; }

  .address {
    position: absolute;
    left: 25px; top: 177px;
    font-size: 13.5px; line-height: 16px;
    font-weight: 500;
  }
  .contact-list {
    position: absolute;
    left: 25px; top: 234px;
    list-style: none;
    font-size: 13px; font-weight: 500;
  }
  .contact-list li {
    display: flex; align-items: center;
    height: 18px; margin-bottom: 7px;
  }
  .contact-list svg { width: 13px; height: 13px; margin-right: 9px; fill: var(--ink); }
  .abn {
    position: absolute;
    left: 25px; top: 316px;
    font-size: 13px; font-weight: 500;
  }
  .abn strong { font-weight: 700; }

  .accent-dot {
    position: absolute;
    left: 388px; top: 180px;
    width: 156px; height: 156px;
    border-radius: 50%;
    background: var(--accent-blue);
  }
</style>
</head>
<body>

<section class="card card--front">
  <div class="brand-name">TBK Plumbing Services</div>

  <div class="holder">
    <div class="holder__name">Rowan Keddle</div>
    <div class="holder__title">Director</div>
  </div>

  <div class="address">
    48 Harbour Crest Road<br>
    Wynnum, QLD 4178
  </div>

  <ul class="contact-list">
    <li>
      <svg viewBox="0 0 24 24" aria-hidden="true"><path d="M6.6 10.8a15.1 15.1 0 0 0 6.6 6.6l2.2-2.2a1 1 0 0 1 1-.25 11.4 11.4 0 0 0 3.6.57 1 1 0 0 1 1 1V20a1 1 0 0 1-1 1A17 17 0 0 1 3 4a1 1 0 0 1 1-1h3.5a1 1 0 0 1 1 1c0 1.25.2 2.45.57 3.57a1 1 0 0 1-.25 1z"/></svg>
      0431 286 517
    </li>
    <li>
      <svg viewBox="0 0 24 24" aria-hidden="true"><path d="M2 5h20v2l-10 7L2 7z M2 9l10 7 10-7v10H2z"/></svg>
      rowan@tbk-plumbing.com.au
    </li>
    <li>
      <svg viewBox="0 0 24 24" aria-hidden="true"><path d="M12 2a10 10 0 1 0 0 20 10 10 0 0 0 0-20zm-1 17.9A8 8 0 0 1 4.2 10.6L9 15.4v1a2 2 0 0 0 2 2zm6.9-2.5a2 2 0 0 0-1.9-1.4h-1v-3a1 1 0 0 0-1-1H8v-2h2a1 1 0 0 0 1-1V7h2a2 2 0 0 0 2-2v-.4a8 8 0 0 1 2.9 12.8z"/></svg>
      www.tbk-plumbing.com.au
    </li>
  </ul>

  <div class="abn"><strong>ABN</strong> - 73 215 904 386</div>

  <div class="accent-dot" aria-hidden="true"></div>
</section>

<section class="card card--back">
  <div class="brand-name">TBK Plumbing Services</div>
</section>

</body>
</html>
```